Consultancy Business Card Design

We need a business card design for a new company based in singapore called KestrelOak. KestrelOak a boutique consultancy firm offering broad-based business solutions, from conception to re-invention, for ventures from new start-ups to long-running traditional businesses.
Its 2 main divisions (Food & Beverage Operations and Construction & Project Management) have access to a wide range of networks, knowledge bases, and resources to service its clients across numerous diverse sectors. This includes, and is not limited to, construction, F&B, and retail.
We are a company that combines the ambition, boldness and energy of one in the 20s with the dedication, level-headedness and dependability of one entering its 30s. Bridging the experiences of the old with ideals of the young, we draw on the positives of both to create a unique synergy.
We hope to see designs that fits our company profile.
Industry/Entity Type
Boutique
Contact Information for Business Card
KestrelOak(Company Name)
Marcus Thiel (Name)
Principle Consultant (Title)
F&B and Hospitality (Division)
(+65) 8043 5617 (Contact no.)
marcus@kestreloak.com.sg (Email)
Colors
Designer to choose colors to be used in the design.

```html
<!DOCTYPE html>
<html lang="en">
<head>
<meta charset="utf-8">
<title>KestrelOak Business Card</title>
<link rel="stylesheet" href="https://fonts.googleapis.com/css2?family=Montserrat:wght@400;500;600&display=swap">
<style>
  :root {
    --backdrop: #e6e6e6;
    --card-dark: #262626;
    --card-dark-edge: #1b1b1b;
    --band-white: #f4f4f4;
    --ink-dark: #1e1e1e;
    --accent-red: #e0393e;
    --text-light: #f2f2f2;
  }
  * { margin: 0; padding: 0; box-sizing: border-box; }
  html, body {
    width: 1200px; height: 900px; overflow: hidden;
    background: var(--backdrop);
    font-family: "Montserrat", sans-serif;
  }
  .stage {
    position: relative; width: 1200px; height: 900px;
    display: flex; justify-content: center; align-items: center; gap: 80px;
  }
  .card {
    position: relative; width: 340px; height: 580px;
    background: radial-gradient(ellipse at 50% 40%, #333 0%, var(--card-dark) 55%, var(--card-dark-edge) 100%);
    box-shadow: 0 14px 30px rgba(0,0,0,0.25);
    overflow: hidden;
  }
  .logo-band {
    position: absolute; left: 0; right: 0; height: 118px;
    background: var(--band-white);
    display: flex; align-items: center; justify-content: center;
  }
  .card-front .logo-band { top: 0; }
  .card-back .logo-band { bottom: 0; }
  .brand-name {
    font-weight: 500; font-size: 38px; letter-spacing: -0.5px;
    color: var(--ink-dark);
  }
  .contact-list {
    position: absolute; top: 150px; left: 0; right: 0;
    display: flex; flex-direction: column; align-items: center; gap: 52px;
    text-align: center;
  }
  .contact-item { display: flex; flex-direction: column; align-items: center; gap: 16px; }
  .icon-box {
    width: 34px; height: 34px; border: 2px solid var(--accent-red);
    display: flex; align-items: center; justify-content: center;
  }
  .icon-box svg { width: 18px; height: 18px; fill: var(--accent-red); }
  .contact-text { font-size: 13px; line-height: 1.45; color: var(--text-light); font-weight: 500; }
  .accent { color: var(--accent-red); }
</style>
</head>
<body>
<main class="stage">
  <section class="card card-front" aria-label="Card front">
    <header class="logo-band"><span class="brand-name">KestrelOak</span></header>
    <div class="contact-list">
      <div class="contact-item">
        <span class="icon-box"><svg viewBox="0 0 20 20"><circle cx="10" cy="6" r="4"/><path d="M2 19c0-5 3.5-7.5 8-7.5s8 2.5 8 7.5z"/></svg></span>
        <p class="contact-text">Marcus Thiel<br><span class="accent">- Principle Consultant -</span><br>F&amp;B and Hospitality</p>
      </div>
      <div class="contact-item">
        <span class="icon-box"><svg viewBox="0 0 20 20"><path d="M5 1.5l3 3.5-1.8 2.2c1 2.3 2.6 3.9 4.6 4.9l2.2-1.8 3.5 3-2 3.2C8.5 16 3.8 11.3 1.8 3.5z"/></svg></span>
        <p class="contact-text"><span class="accent">(+65)</span> 8043 5617</p>
      </div>
      <div class="contact-item">
        <span class="icon-box"><svg viewBox="0 0 20 20"><path d="M1 4h18v1.2L10 11 1 5.2z"/><path d="M1 7.2l9 5.8 9-5.8V16H1z"/></svg></span>
        <p class="contact-text">marcus<span class="accent">@kestreloak.com.sg</span></p>
      </div>
    </div>
  </section>
  <section class="card card-back" aria-label="Card back">
    <footer class="logo-band"><span class="brand-name">KestrelOak</span></footer>
  </section>
</main>
</body>
</html>
```